Packaging Design: Logo/Bottle Design for New Botanical Cocktail Brand

We are a new start up, looking to create a new line of Ready to drink Cocktails. The brand name is Verdance Garden Spritzers, infused with fruit, herb, and floral botanicals grown on our farm in New Hampshire. Flavors will include: Herb flavored with cilantro, Berry- flavored with Ridgeglow Berry, Citrus flavored with lemon Verbena & lemon balm, Pear flavored with Quillon pear, Cucumber & Mint. We need a logo and a label design. There are 2 possible bottles to choose from.

Designer has complete freedom with everything! From fonts and colors to bottle caps and closures. Please view the pinterest link for inspirational bottle designs. https://www.pinboardia.com/dellacravitz/garden-spritzers/

Reason: I am extending the deadline for my project to allow more designers to submit their designs.

Target Market(s)

Female 21 to 48 years old. College educated and professional. The type of person that has a passion for a cause and eats and shops local. People that respect an artisan quality product, hand made by a master craftsman.

Industry/Entity Type

Floral

Requirements
Must have
• Clear Bottle, see options attached. You may also choose your own BUT WE MUST SEE THE LOGO AND IMAGERY ON A BOTTLE
• Logo Design: "Verdance Garden Spritzers"
• Label: We can have front and back, or one continuous label. We are open to painted designs.
• The label must contain the following text in quotes:
• Product Name: " Verdance Garden Spritzers "
• "15% Alc. by Vol. (30 proof)"
• "750 mL"
• "Handcrafted and Bottled by Hollowmere Stillbrook Farm and Distillery
• Winchester, NH-USA"
• The following Text must be in all caps and 3mm in height:
• "Government Warning: (1) According to the Surgeon General, women should not drink alcoholic beverages during pregnancy because of the risk of birth defects. (2) Consumption of alcoholic beverages impairs your ability to drive a car or operate machinery and may cause health problems."
• Must be a space for a bar code: .75 in height by 1.25 in length.
• “www.hollowmerestillbrook.com”
• Must Have the following Statement:
• Infused with fruit, herb, and floral botanicals and sweetened with stevia. Serve cold over ice.
Nice to have
• Antique or vintage botanical illustrations
• https://www.pinboardia.com/dellacravitz/garden-spritzers/
• check out the board for inspiration.
• Think artisanal small batch spirits that are ready to drink out of the bottle. Refreshing flavors just pour over ice and add herb leaves.
• You can use images by doing a search here.
• http://archv.plantrec.example.org/archv/search.xhtml?start=0&collectionFacet=Orchard+Painted+Plate+Archive

```html
<!DOCTYPE html>
<html lang="en">
<head>
<meta charset="utf-8">
<title>Verdance Garden Spritzers – Label Set</title>
<link rel="stylesheet" href="https://fonts.googleapis.com/css2?family=Playfair+Display:wght@400;700&family=Libre+Baskerville&display=swap">
<style>
  :root{
    --bg:#e4e3e6;
    --panel:#d9d8dc;
    --ink:#1d5a63;
    --white:#ffffff;
    --cream:#f7f3e8;
    --cucumber:#a9d89b;
    --cucumber-deep:#1f5a3a;
    --sage:#f4b995;
    --sage-deep:#3f6d73;
    --cilantro:#f4f1ab;
    --cilantro-deep:#1e6670;
    --rosemary:#f3a595;
    --rosemary-deep:#1f7a7a;
  }
  *{box-sizing:border-box;margin:0;padding:0}
  html,body{width:1200px;height:1196px;overflow:hidden}
  body{background:var(--bg);font-family:"Libre Baskerville",serif;color:var(--ink)}
  .label-set{
    width:1200px;height:1196px;padding:6px;
    display:grid;grid-template-columns:repeat(4,1fr);grid-template-rows:repeat(2,1fr);gap:8px;
  }
  .panel{
    background:radial-gradient(ellipse at 50% 55%,#f3f2f4 0%,var(--panel) 75%);
    display:flex;align-items:center;justify-content:center;
  }
  .label{
    position:relative;width:190px;height:500px;
    border-radius:46% 46% 8px 8px / 9% 9% 8px 8px;
    background:var(--tone);overflow:hidden;
    display:flex;flex-direction:column;align-items:center;
  }
  .cucumber{--tone:var(--cucumber);--deep:var(--cucumber-deep)}
  .sage{--tone:var(--sage);--deep:var(--sage-deep)}
  .cilantro{--tone:var(--cilantro);--deep:var(--cilantro-deep)}
  .rosemary{--tone:var(--rosemary);--deep:var(--rosemary-deep)}

  .botanical-art{
    position:absolute;inset:0;
    background:
      radial-gradient(ellipse 60% 22% at 20% 8%,color-mix(in srgb,var(--deep) 55%,transparent),transparent 70%),
      radial-gradient(ellipse 45% 18% at 85% 30%,color-mix(in srgb,var(--deep) 40%,transparent),transparent 70%),
      radial-gradient(ellipse 55% 22% at 30% 88%,color-mix(in srgb,var(--deep) 50%,transparent),transparent 70%),
      radial-gradient(ellipse 40% 15% at 80% 70%,color-mix(in srgb,var(--deep) 30%,transparent),transparent 70%);
  }
  .front-copy{position:relative;width:100%;padding:46px 18px 0;text-align:center;color:var(--white)}
  .brand-name{font-family:"Playfair Display",serif;font-weight:700;font-size:26px;line-height:1}
  .brand-line{font-family:"Playfair Display",serif;font-weight:700;font-size:13px;margin-top:3px}
  .flavor{font-family:"Playfair Display",serif;font-weight:700;font-size:15px;line-height:1.05;margin-top:72px}
  .rule{height:1px;background:var(--white);margin:8px 18px 6px}
  .maker{font-size:6.2px;line-height:1.45}
  .measures{display:flex;justify-content:space-between;margin:10px 22px 0;font-family:"Playfair Display",serif;font-weight:700;font-size:13px}
  .measures small{font-size:7px}

  .back-panel{
    position:absolute;left:10px;right:10px;bottom:14px;top:255px;
    background:color-mix(in srgb,var(--white) 45%,var(--tone));
    border-radius:50% 50% 6px 6px / 16% 16% 6px 6px;
    padding:20px 12px 8px;text-align:center;color:var(--ink);
  }
  .back-panel .brand-name{font-size:20px}
  .back-panel .brand-line{font-size:10px;margin-top:1px}
  .back-panel .rule{background:var(--ink);margin:5px 10px}
  .warning{font-size:5.6px;line-height:1.45;text-transform:uppercase;text-align:justify;margin-top:6px}
  .statement{font-size:6px;line-height:1.45;margin-top:8px;text-align:justify}
  .site{font-size:6px;margin-top:10px}
  .barcode-space{width:42px;height:26px;border:1px solid var(--ink);margin:8px auto 0}
</style>
</head>
<body>
<main class="label-set">

  <section class="panel">
    <article class="label cucumber">
      <div class="botanical-art" role="img" aria-label="Vintage botanical illustration of mint sprigs and cucumber slices"></div>
      <div class="front-copy">
        <p class="brand-name">Verdance</p>
        <p class="brand-line">Garden Spritzers</p>
        <p class="flavor">Cucumber<br>&amp; Mint</p>
        <div class="rule"></div>
        <p class="maker">Handcrafted and Bottled by Hollowmere Stillbrook Farm and Distillery Winchester, NH-USA</p>
        <div class="measures"><span>750<small>mL</small></span><span>15<small>%</small></span></div>
      </div>
    </article>
  </section>

  <section class="panel">
    <article class="label cucumber">
      <div class="back-panel">
        <p class="brand-name">Verdance</p>
        <p class="brand-line">Garden Spritzers</p>
        <div class="rule"></div>
        <p class="warning">Government Warning: (1) According to the Surgeon General, women should not drink alcoholic beverages during pregnancy because of the risk of birth defects. (2) Consumption of alcoholic beverages impairs your ability to drive a car or operate machinery and may cause health problems.</p>
        <p class="statement">Infused with fruit, herb, and floral botanicals and sweetened with stevia. Serve cold over ice.</p>
        <p class="site">www.hollowmerestillbrook.com</p>
        <div class="barcode-space"></div>
      </div>
    </article>
  </section>

  <section class="panel">
    <article class="label sage">
      <div class="botanical-art" role="img" aria-label="Vintage botanical illustration of sage leaves and apple blossoms"></div>
      <div class="front-copy">
        <p class="brand-name">Verdance</p>
        <p class="brand-line">Garden Spritzers</p>
        <p class="flavor">Sage<br>&amp; Apple</p>
        <div class="rule"></div>
        <p class="maker">Handcrafted and Bottled by Hollowmere Stillbrook Farm and Distillery Winchester, NH-USA</p>
        <div class="measures"><span>750<small>mL</small></span><span>15<small>%</small></span></div>
      </div>
    </article>
  </section>

  <section class="panel">
    <article class="label sage">
      <div class="back-panel">
        <p class="brand-name">Verdance</p>
        <p class="brand-line">Garden Spritzers</p>
        <div class="rule"></div>
        <p class="warning">Government Warning: (1) According to the Surgeon General, women should not drink alcoholic beverages during pregnancy because of the risk of birth defects. (2) Consumption of alcoholic beverages impairs your ability to drive a car or operate machinery and may cause health problems.</p>
        <p class="statement">Infused with fruit, herb, and floral botanicals and sweetened with stevia. Serve cold over ice.</p>
        <p class="site">www.hollowmerestillbrook.com</p>
        <div class="barcode-space"></div>
      </div>
    </article>
  </section>

  <section class="panel">
    <article class="label cilantro">
      <div class="botanical-art" role="img" aria-label="Vintage botanical illustration of cilantro leaves and lemons"></div>
      <div class="front-copy">
        <p class="brand-name">Verdance</p>
        <p class="brand-line">Garden Spritzers</p>
        <p class="flavor">Cilantro<br>&amp; Lemon</p>
        <div class="rule"></div>
        <p class="maker">Handcrafted and Bottled by Hollowmere Stillbrook Farm and Distillery Winchester, NH-USA</p>
        <div class="measures"><span>750<small>mL</small></span><span>15<small>%</small></span></div>
      </div>
    </article>
  </section>

  <section class="panel">
    <article class="label cilantro">
      <div class="back-panel">
        <p class="brand-name">Verdance</p>
        <p class="brand-line">Garden Spritzers</p>
        <div class="rule"></div>
        <p class="warning">Government Warning: (1) According to the Surgeon General, women should not drink alcoholic beverages during pregnancy because of the risk of birth defects. (2) Consumption of alcoholic beverages impairs your ability to drive a car or operate machinery and may cause health problems.</p>
        <p class="statement">Infused with fruit, herb, and floral botanicals and sweetened with stevia. Serve cold over ice.</p>
        <p class="site">www.hollowmerestillbrook.com</p>
        <div class="barcode-space"></div>
      </div>
    </article>
  </section>

  <section class="panel">
    <article class="label rosemary">
      <div class="botanical-art" role="img" aria-label="Vintage botanical illustration of rosemary sprigs and small pears"></div>
      <div class="front-copy">
        <p class="brand-name">Verdance</p>
        <p class="brand-line">Garden Spritzers</p>
        <p class="flavor">Rosemary<br>&amp; Pear</p>
        <div class="rule"></div>
        <p class="maker">Handcrafted and Bottled by Hollowmere Stillbrook Farm and Distillery Winchester, NH-USA</p>
        <div class="measures"><span>750<small>mL</small></span><span>15<small>%</small></span></div>
      </div>
    </article>
  </section>

  <section class="panel">
    <article class="label rosemary">
      <div class="back-panel">
        <p class="brand-name">Verdance</p>
        <p class="brand-line">Garden Spritzers</p>
        <div class="rule"></div>
        <p class="warning">Government Warning: (1) According to the Surgeon General, women should not drink alcoholic beverages during pregnancy because of the risk of birth defects. (2) Consumption of alcoholic beverages impairs your ability to drive a car or operate machinery and may cause health problems.</p>
        <p class="statement">Infused with fruit, herb, and floral botanicals and sweetened with stevia. Serve cold over ice.</p>
        <p class="site">www.hollowmerestillbrook.com</p>
        <div class="barcode-space"></div>
      </div>
    </article>
  </section>

</main>
</body>
</html>
```